Ward Compass Business Card Design*

We need a business card design for our company Ward Compass. Our company is specialized in providing online consulting services regarding medical institutions, hospitals and doctors. We work with patients worldwide looking to choose between healthcare providers. We have a website you may use as a reference, where we list doctors and clinics worldwide. So we target Medical providers as well as patients worldwide.
Target Market(s)
Medical Providers and patients around the world
Industry/Entity Type
Medical
Contact Information for Business Card
Salwa Kettani
CEO
+90 612 348 2175
info@wardcompass.example
www.wardcompass.example
14 Annakhil 7 H.R.B. Rabat, Morocco
Requirements
Must have
- Company logo/name on one full side, personal info and smaller logo and company name on the other side.
Nice to have
- Smart and elegant design

```html
<!DOCTYPE html>
<html lang="en">
<head>
<meta charset="utf-8">
<title>Ward Compass Business Card</title>
<link rel="stylesheet" href="https://fonts.googleapis.com/css2?family=Montserrat:wght@300;400;700&family=Roboto:wght@300;400;700&display=swap">
<style>
  :root {
    --navy: #15386a;
    --grey: #8a8a8a;
    --white: #ffffff;
    --backdrop: #e9eaec;
  }
  * { box-sizing: border-box; margin: 0; padding: 0; }
  html, body { width: 1200px; height: 900px; overflow: hidden; }
  body {
    background: var(--backdrop);
    position: relative;
    font-family: "Roboto", Arial, sans-serif;
  }
  .card {
    position: absolute;
    left: 290px;
    width: 620px;
    height: 354px;
    overflow: hidden;
    box-shadow: 0 6px 18px rgba(0,0,0,0.12);
  }
  .card--front { top: 76px; background: var(--navy); }
  .card--back { top: 470px; background: var(--white); }

  .brand {
    display: flex;
    align-items: center;
    gap: 16px;
  }
  .brand__dot {
    border-radius: 50%;
    flex: none;
  }
  .brand__name {
    font-family: "Montserrat", Arial, sans-serif;
    font-weight: 700;
    text-transform: uppercase;
    white-space: nowrap;
  }

  .card--front .brand {
    position: absolute;
    left: 0; right: 0; top: 128px;
    justify-content: center;
  }
  .card--front .brand__dot {
    width: 66px; height: 66px;
    border: 12px solid var(--white);
  }
  .card--front .brand__name {
    color: var(--white);
    font-size: 40px;
    letter-spacing: 1px;
  }
  .front__url {
    position: absolute;
    left: 0; right: 0; top: 252px;
    text-align: center;
    color: var(--white);
    font-family: "Montserrat", Arial, sans-serif;
    font-weight: 400;
    font-size: 15px;
    letter-spacing: 7px;
  }

  .back__wave { position: absolute; inset: 0; }
  .card--back .brand {
    position: absolute;
    left: 34px; top: 146px;
    gap: 10px;
  }
  .card--back .brand__dot {
    width: 36px; height: 36px;
    border: 7px solid var(--navy);
  }
  .card--back .brand__name {
    color: var(--navy);
    font-size: 22px;
  }
  .person {
    position: absolute;
    left: 36px; bottom: 30px;
    color: var(--white);
  }
  .person__name {
    font-family: "Roboto", Arial, sans-serif;
    font-weight: 700;
    font-size: 30px;
    line-height: 1.1;
  }
  .person__role {
    font-weight: 300;
    font-size: 18px;
    margin-top: 2px;
  }
  .contact {
    position: absolute;
    right: 26px; top: 34px;
    color: var(--white);
    text-align: right;
    font-size: 13px;
    font-weight: 300;
    line-height: 1.45;
  }
  .contact__address { margin-right: 28px; }
  .contact__rule {
    width: 30px; height: 2px;
    background: var(--white);
    margin: 8px 28px 10px auto;
  }
  .contact__list { list-style: none; }
  .contact__item {
    display: flex;
    justify-content: flex-end;
    align-items: center;
    gap: 10px;
    margin-bottom: 3px;
  }
  .contact__icon { width: 17px; height: 17px; flex: none; }
</style>
</head>
<body>

<section class="card card--front" aria-label="Card front">
  <div class="brand">
    <span class="brand__dot"></span>
    <span class="brand__name">Ward Compass</span>
  </div>
  <p class="front__url">www.wardcompass.example</p>
</section>

<section class="card card--back" aria-label="Card back">
  <svg class="back__wave" viewBox="0 0 620 354" width="620" height="354" aria-hidden="true">
    <path d="M0,262 C150,242 262,232 322,160 C384,82 450,14 600,-8 L620,-8 L620,354 L0,354 Z" fill="var(--grey)"/>
    <path d="M0,272 C150,252 270,242 330,170 C392,92 458,24 620,6 L620,354 L0,354 Z" fill="var(--navy)"/>
  </svg>

  <div class="brand">
    <span class="brand__dot"></span>
    <span class="brand__name">Ward Compass</span>
  </div>

  <div class="person">
    <p class="person__name">Salwa Kettani</p>
    <p class="person__role">CEO</p>
  </div>

  <div class="contact">
    <p class="contact__address">14 Annakhil<br>7 H.R.B. Rabat, Morocco</p>
    <div class="contact__rule"></div>
    <ul class="contact__list">
      <li class="contact__item">+90 612 348 2175
        <svg class="contact__icon" viewBox="0 0 20 20" aria-hidden="true"><circle cx="10" cy="10" r="10" fill="var(--white)"/><path d="M6.5 5.5l2 0 .8 2.6-1.2 1c.7 1.3 1.5 2.1 2.8 2.8l1-1.2 2.6.8 0 2c-4.5.4-8.4-3.5-8-8z" fill="var(--navy)"/></svg>
      </li>
      <li class="contact__item">info@wardcompass.example
        <svg class="contact__icon" viewBox="0 0 20 20" aria-hidden="true"><rect x="2" y="4.5" width="16" height="11" fill="var(--white)"/><path d="M2 4.5l8 6 8-6" fill="none" stroke="var(--navy)" stroke-width="1.3"/></svg>
      </li>
      <li class="contact__item">www.wardcompass.example
        <svg class="contact__icon" viewBox="0 0 20 20" aria-hidden="true"><circle cx="10" cy="10" r="9" fill="var(--white)"/><g fill="none" stroke="var(--navy)" stroke-width="1.1"><circle cx="10" cy="10" r="6"/><ellipse cx="10" cy="10" rx="2.6" ry="6"/><path d="M4 10h12"/></g></svg>
      </li>
    </ul>
  </div>
</section>

</body>
</html>
```